Road Construction Company needs business cards

We would like a new business card designed for our business.

We're a road construction company based in Qld, Australia.

Can the business card please have the following information on it.

Name: Warren Halbeck
Position: General Manager
Phone: 0472 915 348
Email: Warren.halbeck@tovrin.com.au
Address: 87 Marrow Ave, Pendlebay, QLD, 4023
Website: www.tovrin.com.au

Visually we'd like the card to be professional and simple.

Attached is our logo.

Our website is www.tovrin.com.au

Target Market(s)

Men aged 25-60

Contact Information for Business Card

As listed in project description

Font styles to use
Serif

Requirements
Must have
• Large logo on back of card

```html
<!DOCTYPE html>
<html lang="en">
<head>
<meta charset="utf-8">
<title>Tovrin Road Construction – Business Card</title>
<link rel="stylesheet" href="https://fonts.googleapis.com/css2?family=Open+Sans:wght@400;600;800&display=swap">
<style>
  :root {
    --bg: #16171a;
    --card: #212125;
    --card-deep: #141416;
    --brand-blue: #1a5cb0;
    --accent-blue: #3ea6de;
    --text-light: #f2f2f2;
    --pattern-light: #8d8f94;
  }
  * { margin: 0; padding: 0; box-sizing: border-box; }
  html, body { width: 1200px; height: 780px; overflow: hidden; background: var(--bg); }
  body { font-family: "Open Sans", Arial, sans-serif; position: relative; }

  .card {
    position: absolute;
    top: 225px;
    width: 540px;
    height: 330px;
    background: var(--card);
    border-left: 4px solid var(--accent-blue);
    overflow: hidden;
  }
  .card--front { left: 30px; }
  .card--back  { left: 630px; }

  /* Front */
  .brand-name {
    position: absolute;
    font-family: "Open Sans", Arial, sans-serif;
    font-weight: 800;
    color: var(--brand-blue);
    letter-spacing: 2px;
    text-transform: uppercase;
    line-height: 1;
  }
  .card--front .brand-name { left: 34px; top: 30px; font-size: 46px; }

  .contact {
    position: absolute;
    left: 30px;
    top: 150px;
    color: var(--text-light);
    font-size: 14px;
    line-height: 1.45;
    list-style: none;
  }
  .contact .address { margin-bottom: 4px; }
  .contact li { display: flex; align-items: center; gap: 8px; }
  .contact svg { width: 12px; height: 12px; flex: none; fill: var(--text-light); }
  .contact .address-line { padding-left: 0; }

  .person {
    position: absolute;
    right: 46px;
    top: 150px;
    text-align: right;
  }
  .person-name { color: var(--accent-blue); font-size: 29px; font-weight: 600; line-height: 1.1; }
  .person-role { color: var(--text-light); font-size: 17px; font-weight: 400; margin-top: 2px; }

  .side-tab {
    position: absolute;
    right: 0;
    top: 196px;
    width: 16px;
    height: 46px;
    background: var(--accent-blue);
  }

  /* Back */
  .pattern-field {
    position: absolute;
    inset: 0;
    background: linear-gradient(100deg, var(--card-deep) 0%, var(--card) 55%, var(--pattern-light) 100%);
  }
  .card--back .brand-name {
    left: 0; right: 0; top: 118px;
    text-align: center;
    font-size: 92px;
  }
</style>
</head>
<body>
  <section class="card card--front" aria-label="Card front">
    <div class="brand-name">Tovrin</div>

    <ul class="contact">
      <li class="address-line">87 Marrow Ave,</li>
      <li class="address-line address">Pendlebay, QLD, 4023</li>
      <li>
        <svg viewBox="0 0 24 24" aria-hidden="true"><path d="M6.6 10.8a15.1 15.1 0 0 0 6.6 6.6l2.2-2.2c.3-.3.7-.4 1-.2 1.1.4 2.3.6 3.6.6.6 0 1 .4 1 1V20c0 .6-.4 1-1 1A17 17 0 0 1 3 4c0-.6.4-1 1-1h3.5c.6 0 1 .4 1 1 0 1.3.2 2.5.6 3.6.1.3 0 .7-.2 1z"/></svg>
        0472 915 348
      </li>
      <li>
        <svg viewBox="0 0 24 24" aria-hidden="true"><path d="M12 2a10 10 0 1 0 0 20 10 10 0 0 0 0-20zm6.9 6h-3a15 15 0 0 0-1.3-3.9A8 8 0 0 1 18.9 8zM12 4c.8 1.2 1.5 2.5 1.9 4h-3.8c.4-1.5 1.1-2.8 1.9-4zM4.3 14a8 8 0 0 1 0-4h3.4a16 16 0 0 0 0 4zm.8 2h3a15 15 0 0 0 1.3 3.9A8 8 0 0 1 5.1 16zm3-8h-3a8 8 0 0 1 4.3-3.9A15 15 0 0 0 8.1 8zM12 20c-.8-1.2-1.5-2.5-1.9-4h3.8c-.4 1.5-1.1 2.8-1.9 4zm2.3-6H9.7a14 14 0 0 1 0-4h4.6a14 14 0 0 1 0 4zm.3 5.9a15 15 0 0 0 1.3-3.9h3a8 8 0 0 1-4.3 3.9zm1.7-5.9a16 16 0 0 0 0-4h3.4a8 8 0 0 1 0 4z"/></svg>
        www.tovrin.com.au
      </li>
      <li>
        <svg viewBox="0 0 24 24" aria-hidden="true"><path d="M3 5h18c.6 0 1 .4 1 1v12c0 .6-.4 1-1 1H3c-.6 0-1-.4-1-1V6c0-.6.4-1 1-1zm9 7.2L4.4 7H4v1.2l8 5.6 8-5.6V7h-.4z"/></svg>
        Warren.halbeck@tovrin.com.au
      </li>
    </ul>

    <div class="person">
      <div class="person-name">Warren Halbeck</div>
      <div class="person-role">General Manager</div>
    </div>
    <div class="side-tab"></div>
  </section>

  <section class="card card--back" aria-label="Card back">
    <div class="pattern-field" role="img" aria-label="Repeating dark chevron pattern fading to silver on the right"></div>
    <div class="brand-name">Tovrin</div>
  </section>
</body>
</html>
```